Boutique custom software development company needs new business card

Our nearly 20 year old custom software development company would like to better include the fact that we are now providing Bitcoin services. These new services are B2B include education (how to acquire and securely hold Bitcoin) and integrating Bitcoin payments into existing ecommerce sites or other existing systems. Please keep the card clean and simple. Attached is our current design and some other files. vextorial.com

Target Market(s)

businesses owners interested in long term relationship

Industry/Entity Type

Custom software development and Bitcoin

Contact Information for Business Card

Dale Parker, dale@vextorial.com, vextorial.com, (888) 555-VXTRL

Font styles to use
Other font styles liked:
• monospace

Requirements
Must have
• double-sided
Nice to have
• clean and simple
Should not have
• physical address

```html
<!DOCTYPE html>
<html lang="en">
<head>
<meta charset="utf-8">
<title>Vextorial business card</title>
<link rel="stylesheet" href="https://fonts.googleapis.com/css2?family=Lato:wght@300;400;700&family=Montserrat:wght@700;800&display=swap">
<style>
  :root {
    --bg: #dcdcdc;
    --paper: #ffffff;
    --blue: #2f72c4;
    --orange: #f97d16;
    --ink: #555555;
    --shadow: 0 10px 30px rgba(0,0,0,.18);
  }
  * { box-sizing: border-box; margin: 0; padding: 0; }
  html, body { width: 1200px; height: 1056px; overflow: hidden; }
  body {
    background: var(--bg);
    font-family: "Lato", Arial, sans-serif;
    position: relative;
  }
  .card {
    position: absolute;
    left: 220px;
    width: 760px;
    height: 434px;
    box-shadow: var(--shadow);
    overflow: hidden;
  }
  /* front */
  .card--front { top: 60px; background: var(--paper); }
  .brand {
    position: absolute;
    left: 300px;
    top: 70px;
  }
  .brand__name {
    font-family: "Montserrat", Arial, sans-serif;
    font-weight: 800;
    font-size: 60px;
    letter-spacing: 1px;
    line-height: 1;
    color: var(--blue);
  }
  .brand__tagline {
    margin-top: 10px;
    font-size: 20px;
    line-height: 1.25;
    color: var(--blue);
  }
  .brand__tagline-accent { color: var(--orange); font-weight: 700; }
  .name-band {
    position: absolute;
    left: 0;
    top: 200px;
    width: 410px;
    height: 130px;
    background: var(--blue);
    border-radius: 0 12px 12px 0;
    padding: 26px 28px 0 0;
    text-align: right;
  }
  .name-band__name {
    font-family: "Montserrat", Arial, sans-serif;
    font-weight: 800;
    font-size: 34px;
    letter-spacing: 1px;
    text-transform: uppercase;
    color: var(--paper);
    line-height: 1.1;
  }
  .name-band__first { color: var(--orange); }
  .name-band__role {
    margin-top: 4px;
    font-weight: 300;
    font-size: 21px;
    color: var(--paper);
  }
  .contacts {
    position: absolute;
    left: 432px;
    top: 240px;
    list-style: none;
  }
  .contacts__item {
    display: flex;
    align-items: center;
    gap: 12px;
    font-size: 21px;
    color: var(--ink);
    margin-bottom: 12px;
  }
  .contacts__icon {
    width: 26px;
    height: 26px;
    border-radius: 4px;
    background: var(--orange);
    display: flex;
    align-items: center;
    justify-content: center;
    flex: none;
  }
  /* back */
  .card--back { top: 562px; background: var(--blue); }
  .back__band {
    position: absolute;
    left: 0; top: 0;
    width: 100%;
    height: 150px;
    background: var(--orange);
  }
  .back__square {
    position: absolute;
    left: 290px;
    top: 60px;
    width: 180px;
    height: 180px;
    background: var(--blue);
    display: flex;
    align-items: center;
    justify-content: center;
  }
  .back__name {
    font-family: "Montserrat", Arial, sans-serif;
    font-weight: 800;
    font-size: 30px;
    color: var(--paper);
    letter-spacing: 1px;
  }
  .back__url {
    position: absolute;
    left: 0; width: 100%;
    top: 256px;
    text-align: center;
    font-size: 24px;
    color: var(--paper);
  }
  .back__services {
    position: absolute;
    left: 0; width: 100%;
    top: 310px;
    text-align: center;
    font-size: 19px;
    font-weight: 300;
    color: var(--paper);
    line-height: 1.5;
  }
  .back__services strong { font-weight: 700; color: var(--orange); }
</style>
</head>
<body>
  <section class="card card--front">
    <div class="brand">
      <div class="brand__name">VEXTORIAL</div>
      <div class="brand__tagline">developer of custom applications<br><span class="brand__tagline-accent">&amp; Bitcoin services</span></div>
    </div>
    <div class="name-band">
      <div class="name-band__name"><span class="name-band__first">Dale</span> Parker</div>
      <div class="name-band__role">Software Developer</div>
    </div>
    <ul class="contacts">
      <li class="contacts__item">
        <span class="contacts__icon">
          <svg width="16" height="16" viewBox="0 0 24 24"><path fill="#fff" d="M6.6 10.8a15.1 15.1 0 0 0 6.6 6.6l2.2-2.2c.3-.3.7-.4 1-.2 1.1.4 2.3.6 3.6.6.6 0 1 .4 1 1V20c0 .6-.4 1-1 1C10.6 21 3 13.4 3 4c0-.6.4-1 1-1h3.5c.6 0 1 .4 1 1 0 1.3.2 2.5.6 3.6.1.3 0 .7-.2 1z"/></svg>
        </span>
        (888) 555-VXTRL
      </li>
      <li class="contacts__item">
        <span class="contacts__icon">
          <svg width="18" height="14" viewBox="0 0 18 14"><rect x="1" y="1" width="16" height="12" fill="none" stroke="#fff" stroke-width="1.6"/><path d="M1 1l8 7 8-7" fill="none" stroke="#fff" stroke-width="1.6"/></svg>
        </span>
        dale@vextorial.com
      </li>
      <li class="contacts__item">
        <span class="contacts__icon">
          <svg width="14" height="16" viewBox="0 0 14 16"><path fill="#fff" d="M2 1l10 7-4.5.6L10 14l-2 1-2.5-5.4L2 12z"/></svg>
        </span>
        vextorial.com
      </li>
    </ul>
  </section>

  <section class="card card--back">
    <div class="back__band"></div>
    <div class="back__square"><span class="back__name">vextorial</span></div>
    <div class="back__url">vextorial.com</div>
    <div class="back__services"><strong>Bitcoin for business</strong><br>Education &amp; secure custody · Payment integration</div>
  </section>
</body>
</html>
```